New Website for Manufacturing Company - PSD only, no coding - CLOSED TO NEW DESIGNERS

IF YOU HAVE NOT ALREADY SUBMITTED A DESIGN PLEASE DO NOT SUBMIT ONE.
This is a re-work of an existing website. We can keep the themes and color schemes the same but we will be changing the layout and page content.
The scope includes the creation of some icons/sketches that will form some of the page content.
The scope is design only, no coding.
There are four files that have been uploaded that give a more detailed project brief, please read them.
Target Market(s)
Manufacturing
Industry/Entity Type
It Company
Number of Pages Required
1 page

```html
<!DOCTYPE html>
<html lang="en">
<head>
<meta charset="utf-8">
<title>Kestrel – High Temperature Insulation Experts</title>
<link href="https://fonts.googleapis.com/css2?family=Open+Sans:wght@400;600;700;800&display=swap" rel="stylesheet">
<style>
:root{
  --navy:#1f2730;
  --nav-active:#131920;
  --blue:#1f76bb;
  --blue-dark:#165a91;
  --page:#ffffff;
  --hero-bg:#e9eaec;
  --text:#4a4f55;
  --muted:#8a9096;
  --tile:#e4e6e8;
  --tile-edge:#d2d5d8;
  --footer:#2a2e33;
  --footer-deep:#1c1f23;
  --footer-text:#a7adb3;
}
*{box-sizing:border-box;margin:0;padding:0}
html,body{width:843px;height:1200px;overflow:hidden}
body{font-family:"Open Sans",Arial,sans-serif;background:var(--page);color:var(--text);position:relative}

/* header */
.site-header{position:absolute;top:0;left:0;width:843px;height:86px;background:#fff}
.brand{position:absolute;left:40px;top:24px;display:flex;align-items:center;gap:8px}
.brand-square{width:12px;height:12px;background:var(--blue)}
.brand-name{font-weight:800;font-size:28px;color:var(--blue);letter-spacing:.5px;line-height:1}
.tagline{position:absolute;left:206px;top:36px;font-size:11px;color:var(--navy);font-weight:600;white-space:nowrap}
.account-bar{position:absolute;right:40px;top:0;height:16px;background:var(--navy);color:#fff;font-size:8px;display:flex;gap:12px;align-items:center;padding:0 10px}
.contact-item{position:absolute;top:32px;display:flex;gap:8px;align-items:center}
.contact-item .icon{width:26px;height:26px;border-radius:50%;background:var(--blue);display:flex;align-items:center;justify-content:center}
.contact-item .label{font-size:8px;line-height:1.35;color:var(--muted)}
.contact-item .label b{color:var(--navy);font-weight:600;display:block}
.contact-email{left:560px}
.contact-call{left:700px}

/* nav */
.main-nav{position:absolute;top:86px;left:0;width:843px;height:28px;background:var(--navy);display:flex;align-items:center;padding-left:40px}
.main-nav a{color:#d9dde1;font-size:9px;text-decoration:none;height:28px;line-height:28px;padding:0 20px}
.main-nav a.active{background:var(--nav-active);color:#fff}
.main-nav .search{position:absolute;right:44px;top:8px}

/* hero */
.hero{position:absolute;top:114px;left:0;width:843px;height:322px;background:var(--hero-bg)}
.slider{position:absolute;left:42px;top:48px;width:758px;height:260px;border:6px solid #fff;box-shadow:0 2px 8px rgba(0,0,0,.25);overflow:hidden}
.slider svg{position:absolute;left:0;top:0}
.slide-copy{position:absolute;left:560px;top:30px;width:180px;color:#fff}
.slide-copy h1{font-size:18px;font-weight:700;margin-bottom:10px}
.slide-copy .lead{font-size:10px;color:#4ea3e6;font-weight:600;line-height:1.35;margin-bottom:10px}
.slide-copy p{font-size:8px;line-height:1.5;color:#e1e5e9}
.slide-copy .more{position:absolute;right:6px;top:188px;font-size:9px;color:#4ea3e6}
.slider-dots{position:absolute;left:50%;bottom:10px;transform:translateX(-130px);display:flex;gap:5px}
.slider-dots span{width:5px;height:5px;border-radius:50%;background:#9aa3ab}
.slider-dots span.on{background:#fff}

/* welcome */
.welcome{position:absolute;top:500px;left:0;width:843px;text-align:center}
.welcome h2{font-size:19px;font-weight:700;color:var(--navy)}
.welcome .rule{width:60px;height:2px;background:var(--blue);margin:6px auto 8px}
.welcome p{width:560px;margin:0 auto;font-size:8px;line-height:1.6;color:var(--muted)}

.capabilities{position:absolute;top:590px;left:70px;width:703px;display:grid;grid-template-columns:repeat(4,1fr);row-gap:22px}
.capability{text-align:center}
.capability svg{display:block;margin:0 auto}
.capability h3{font-size:10px;font-weight:600;color:var(--navy);margin-top:6px}

.view-all{position:absolute;top:942px;left:371px;width:102px;height:22px;background:var(--blue);color:#fff;font-size:9px;font-weight:600;display:flex;align-items:center;justify-content:center;gap:6px;transform:skewX(-20deg)}
.view-all span{transform:skewX(20deg);display:flex;gap:6px;align-items:center}

/* footer */
.site-footer{position:absolute;top:1004px;left:0;width:843px;height:154px;background:var(--footer);padding:22px 0 0 68px;display:flex;gap:0}
.footer-col{width:150px}
.footer-col h4{font-size:9px;color:#fff;font-weight:600;margin-bottom:8px;letter-spacing:.3px}
.footer-col li{list-style:none;font-size:8px;color:var(--footer-text);line-height:1.8;display:flex;align-items:center;gap:5px}
.footer-col li::before{content:"";width:3px;height:3px;background:var(--blue);display:inline-block}
.footer-col.contact li::before{display:none}
.social{display:flex;gap:6px}
.social span{width:20px;height:20px;background:var(--blue)}
.bottom-bar{position:absolute;top:1158px;left:0;width:843px;height:42px;background:var(--footer-deep);color:var(--footer-text);font-size:8px;display:flex;align-items:center;justify-content:space-between;padding:0 40px 0 68px}
</style>
</head>
<body>

<header class="site-header">
  <div class="brand"><span class="brand-square"></span><span class="brand-name">KESTREL</span></div>
  <div class="tagline">" High Temperature Insulation Experts "</div>
  <div class="account-bar"><span>Login</span><span>Register</span></div>
  <div class="contact-item contact-email">
    <span class="icon"><svg width="12" height="9" viewBox="0 0 12 9"><rect x=".5" y=".5" width="11" height="8" fill="none" stroke="#fff"/><path d="M.5 .5 6 5 11.5 .5" fill="none" stroke="#fff"/></svg></span>
    <span class="label">Email<b>info@kestrelthermal.com</b></span>
  </div>
  <div class="contact-item contact-call">
    <span class="icon"><svg width="11" height="11" viewBox="0 0 24 24"><path fill="#fff" d="M6.6 10.8c1.4 2.8 3.8 5.1 6.6 6.6l2.2-2.2c.3-.3.7-.4 1-.2 1.1.4 2.3.6 3.6.6.6 0 1 .4 1 1V20c0 .6-.4 1-1 1C10.6 21 3 13.4 3 4c0-.6.4-1 1-1h3.5c.6 0 1 .4 1 1 0 1.3.2 2.5.6 3.6.1.3 0 .7-.2 1z"/></svg></span>
    <span class="label">Call Now<b>555-014-2280</b></span>
  </div>
</header>

<nav class="main-nav">
  <a class="active">Home</a><a>Who</a><a>Industrial</a><a>Custom Manufacturing</a><a>About Us</a><a>Contact Us</a>
  <svg class="search" width="12" height="12" viewBox="0 0 12 12"><circle cx="5" cy="5" r="3.8" fill="none" stroke="#fff" stroke-width="1.5"/><path d="M8 8l3 3" stroke="#fff" stroke-width="1.6"/></svg>
</nav>

<section class="hero">
  <div class="slider">
    <svg width="746" height="248" viewBox="0 0 746 248">
      <defs>
        <linearGradient id="photoTone" x1="0" y1="0" x2="1" y2="1">
          <stop offset="0" stop-color="#f2f4f6"/><stop offset="1" stop-color="#b9c2ca"/>
        </linearGradient>
      </defs>
      <rect width="746" height="248" fill="#2a3036"/>
      <polygon points="0,0 560,0 430,248 0,248" fill="var(--blue)"/>
      <polygon points="0,0 220,0 470,248 0,248" fill="var(--blue-dark)" opacity=".45"/>
      <rect x="70" y="30" width="270" height="185" fill="url(#photoTone)" role="img" aria-label="Photo of a high temperature insulation product assembly"/>
    </svg>
    <div class="slide-copy">
      <h1>Welcome To Kestrel</h1>
      <div class="lead">The Industry Leader and Specialist of High-Temperature Insulating Materials</div>
      <p>Excellent insulating properties, low thermal conductivity, excellent thermal shock resistance, and low storage capacity in a custom size, cut and finish.</p>
      <span class="more">Read More &rsaquo;</span>
    </div>
    <div class="slider-dots"><span class="on"></span><span></span><span></span></div>
  </div>
</section>

<section class="welcome">
  <h2>WELCOME TO OUR WEBSITE</h2>
  <div class="rule"></div>
  <p>Excellent insulating properties, low thermal conductivity, excellent thermal shock resistance, and low heat storage capacity. Custom parts for kilns, furnaces, laboratory ovens, foundry ladles and more. From cutting and laminating to forming and machining, we shape insulation to your exact specification.</p>
</section>

<section class="capabilities">
  <div class="capability">
    <svg width="120" height="105" viewBox="0 0 120 105"><polygon points="22,8 116,8 98,97 4,97" fill="var(--tile)" stroke="var(--tile-edge)"/><rect x="34" y="24" width="52" height="56" fill="#c9ced3" role="img" aria-label="Waterjet cutting sketch"/></svg>
    <h3>Waterjet</h3>
  </div>
  <div class="capability">
    <svg width="120" height="105" viewBox="0 0 120 105"><polygon points="22,8 116,8 98,97 4,97" fill="var(--tile)" stroke="var(--tile-edge)"/><rect x="34" y="24" width="52" height="56" fill="#c9ced3" role="img" aria-label="Casting sketch"/></svg>
    <h3>Casting</h3>
  </div>
  <div class="capability">
    <svg width="120" height="105" viewBox="0 0 120 105"><polygon points="22,8 116,8 98,97 4,97" fill="var(--tile)" stroke="var(--tile-edge)"/><rect x="34" y="24" width="52" height="56" fill="#c9ced3" role="img" aria-label="Laminating sketch"/></svg>
    <h3>Laminating</h3>
  </div>
  <div class="capability">
    <svg width="120" height="105" viewBox="0 0 120 105"><polygon points="22,8 116,8 98,97 4,97" fill="var(--tile)" stroke="var(--tile-edge)"/><rect x="34" y="24" width="52" height="56" fill="#c9ced3" role="img" aria-label="Slitting sketch"/></svg>
    <h3>Slitting</h3>
  </div>
  <div class="capability">
    <svg width="120" height="105" viewBox="0 0 120 105"><polygon points="22,8 116,8 98,97 4,97" fill="var(--tile)" stroke="var(--tile-edge)"/><rect x="34" y="24" width="52" height="56" fill="#c9ced3" role="img" aria-label="CNC machining sketch"/></svg>
    <h3>CNC Machining</h3>
  </div>
  <div class="capability">
    <svg width="120" height="105" viewBox="0 0 120 105"><polygon points="22,8 116,8 98,97 4,97" fill="var(--tile)" stroke="var(--tile-edge)"/><rect x="34" y="24" width="52" height="56" fill="#c9ced3" role="img" aria-label="Diecutting sketch"/></svg>
    <h3>Diecutting</h3>
  </div>
  <div class="capability">
    <svg width="120" height="105" viewBox="0 0 120 105"><polygon points="22,8 116,8 98,97 4,97" fill="var(--tile)" stroke="var(--tile-edge)"/><rect x="34" y="24" width="52" height="56" fill="#c9ced3" role="img" aria-label="Vacuum forming sketch"/></svg>
    <h3>Vacuum Forming</h3>
  </div>
  <div class="capability">
    <svg width="120" height="105" viewBox="0 0 120 105"><polygon points="22,8 116,8 98,97 4,97" fill="var(--tile)" stroke="var(--tile-edge)"/><rect x="34" y="24" width="52" height="56" fill="#c9ced3" role="img" aria-label="Waterjet sketch"/></svg>
    <h3>Waterjet</h3>
  </div>
</section>

<div class="view-all"><span>View All <svg width="8" height="8" viewBox="0 0 8 8"><path d="M1 4h6M4 1l3 3-3 3" stroke="#fff" fill="none" stroke-width="1.3"/></svg></span></div>

<footer class="site-footer">
  <div class="footer-col"><h4>CAPABILITIES</h4><ul><li>Cutting</li><li>Vacuum Forming</li><li>Gluing / Diecutting</li><li>CNC Machine</li></ul></div>
  <div class="footer-col"><h4>SERVICES</h4><ul><li>Design</li><li>Rapid Prototyping</li><li>Design</li><li>Rapid Prototyping</li></ul></div>
  <div class="footer-col"><h4>MATERIALS</h4><ul><li>Design</li><li>Rapid Prototyping</li><li>Design</li><li>Rapid Prototyping</li></ul></div>
  <div class="footer-col contact"><h4>CONTACT US</h4><ul><li>555-014-2280</li><li>info@kestrelthermal.com</li><li>42 Harbor Way, Marden, MA 01900</li></ul></div>
  <div class="footer-col"><h4>FOLLOW US</h4><div class="social"><span></span><span></span><span></span><span></span></div></div>
</footer>
<div class="bottom-bar"><span>Copyright © 2014 Kestrel Thermal</span><span>TOP</span></div>

</body>
</html>
```